NZ First of it's kind solutions directory and marketplace for busy Mums needs a business card design

We need a business card design for our new nationwide business in NZ (long term plans to go global). We provide solutions to the everyday challenges that busy Mums face by connecting them with quality communities and suppliers of carefully selected, relevant products and services. We sell direct via our online marketplace. The final design should communicate our values of inclusivity, quality and smart solutions. Colours should incorporate our logo colour palette of #477077 and #6ba8b2. Our website is at https://www.brightnestmums.example

Target Market(s)

busy Mums, Age 28 – 50, female, income over $100K, location main centres NZ primarily but NZ wide. Is likely juggling work or career with a young family. Probably had hobbies which have fallen by the wayside.
-Wants to succeed in her chosen career without compromising on family life
-to successfully juggle her career without feeling like she is compromising her children
- Is time poor, something always has to give and it’s generally her health (she’ll stay up late, get stressed)
- probably ex corporate or professional career. Has discretional income

Industry/Entity Type

Business

Contact Information for Business Card

Lena Forbisher, Founder, BrightNestMums.example (Strapline Tap; Gather; Sorted), 47 Kowhai Terrace, Ellerslie, Auckland 1051, New Zealand. Mob: 021 483 517 Ph: +64 (0)9 571 4860

Font styles to use
Other font styles liked:
• Raleway, and/or Architects Daughter

Colors
00a990
33b8a4
86cfc6
cfeae6

Requirements
Must have
• the above details, streamline. the logo and colours associated with those logos
Should not have
• foil or metallic colours

```html
<!DOCTYPE html>
<html lang="en">
<head>
<meta charset="utf-8">
<title>BrightNestMums – Business Card</title>
<link rel="stylesheet" href="https://fonts.googleapis.com/css2?family=Raleway:wght@400;500;700;800&display=swap">
<style>
  :root {
    --teal-deep: #477077;
    --teal-soft: #6ba8b2;
    --card-white: #ffffff;
    --ink: #3d3d3d;
    --ghost: #f5f5f5;
    --backdrop: #2a2a2a;
  }
  * { box-sizing: border-box; margin: 0; padding: 0; }
  html, body {
    width: 1189px; height: 1200px; overflow: hidden;
    background: var(--backdrop);
    font-family: "Raleway", sans-serif;
  }
  .canvas { position: relative; width: 1189px; height: 1200px; }
  .card {
    position: absolute; left: 171px; width: 856px; height: 490px;
    overflow: hidden;
    box-shadow: 0 6px 18px rgba(0,0,0,.45);
  }
  .card--front { top: 66px; background: var(--teal-soft); }
  .card--back { top: 625px; background: var(--card-white); }

  .brand { position: absolute; display: flex; align-items: center; gap: 16px; }
  .brand__dot { border-radius: 50%; flex: none; }
  .brand__name { font-weight: 800; letter-spacing: -0.5px; line-height: 1; }

  .card--front .brand { left: 0; right: 0; top: 212px; justify-content: center; }
  .card--front .brand__dot { width: 42px; height: 42px; background: var(--card-white); }
  .card--front .brand__name { color: var(--card-white); font-size: 58px; }
  .front-url {
    position: absolute; left: 0; right: 0; top: 352px; text-align: center;
    color: var(--card-white); font-size: 19px; letter-spacing: 2.6px;
  }
  .front-url strong { font-weight: 700; }

  .ghost-mark {
    position: absolute; left: 517px; top: 118px; width: 326px; height: 326px;
    border-radius: 50%; background: var(--ghost);
  }
  .card--back .brand { left: 44px; top: 84px; }
  .card--back .brand__dot { width: 34px; height: 34px; background: var(--teal-soft); }
  .card--back .brand__name { color: var(--teal-deep); font-size: 46px; }

  .person { position: absolute; left: 45px; top: 294px; }
  .person__name { font-size: 27px; font-weight: 800; letter-spacing: -0.5px; line-height: 1; }
  .person__first { color: var(--teal-deep); }
  .person__last { color: var(--teal-soft); }
  .person__role { font-size: 19px; color: var(--ink); font-weight: 500; margin-top: 2px; }
  .rule {
    position: absolute; left: 140px; top: 343px; width: 678px; height: 1.5px;
    background: var(--teal-soft);
  }

  .contacts { position: absolute; left: 45px; top: 382px; list-style: none; }
  .contacts li {
    display: flex; align-items: center; gap: 8px;
    font-size: 20px; color: var(--ink); height: 27px;
  }
  .contacts svg { width: 24px; height: 24px; flex: none; }

  .address {
    position: absolute; right: 43px; top: 382px; text-align: right;
    font-size: 20px; color: var(--ink); line-height: 27px; font-style: normal;
  }
</style>
</head>
<body>
<main class="canvas">
  <section class="card card--front" aria-label="Business card front">
    <div class="brand">
      <span class="brand__dot"></span>
      <span class="brand__name">BrightNestMums</span>
    </div>
    <p class="front-url">www.<strong>brightnestmums</strong>.example</p>
  </section>

  <section class="card card--back" aria-label="Business card back">
    <div class="ghost-mark" aria-hidden="true"></div>
    <div class="brand">
      <span class="brand__dot"></span>
      <span class="brand__name">BrightNestMums</span>
    </div>

    <div class="person">
      <p class="person__name"><span class="person__first">Lena</span> <span class="person__last">Forbisher</span></p>
      <p class="person__role">Founder</p>
    </div>
    <div class="rule"></div>

    <ul class="contacts">
      <li>
        <svg viewBox="0 0 24 24" aria-label="Mobile"><circle cx="12" cy="12" r="10.5" fill="none" stroke="#6ba8b2" stroke-width="1.5"/><rect x="8.5" y="6" width="7" height="12" rx="1.2" fill="none" stroke="#6ba8b2" stroke-width="1.4"/></svg>
        021 483 517
      </li>
      <li>
        <svg viewBox="0 0 24 24" aria-label="Phone"><circle cx="12" cy="12" r="10.5" fill="none" stroke="#6ba8b2" stroke-width="1.5"/><path d="M6.5 10.5c0-2 11-2 11 0v1h-3v-1h-5v1h-3z" fill="#6ba8b2"/><rect x="8" y="12" width="8" height="5" rx="1" fill="#6ba8b2"/></svg>
        +64 (0)9 571 4860
      </li>
      <li>
        <svg viewBox="0 0 24 24" aria-label="Website"><circle cx="12" cy="12" r="10.5" fill="none" stroke="#6ba8b2" stroke-width="1.5"/><circle cx="12" cy="12" r="6.5" fill="none" stroke="#6ba8b2" stroke-width="1.2"/><ellipse cx="12" cy="12" rx="3" ry="6.5" fill="none" stroke="#6ba8b2" stroke-width="1"/><path d="M5.5 12h13M6.5 9h11M6.5 15h11" stroke="#6ba8b2" stroke-width="1"/></svg>
        www.brightnestmums.example
      </li>
    </ul>

    <address class="address">
      47 Kowhai Terrace,<br>
      Ellerslie, Auckland 1051<br>
      New Zealand
    </address>
  </section>
</main>
</body>
</html>
```